Web Design For Marlow Pool Service

We are working with a company that wants a website for their pool service. Some sites to use for content/competitors and inspiration:
https://sacramento.brightwaterpoolco.example/builder/newbuild/repair/ppc
https://hollowbrookpoolcareplus.example/
https://lakemontpoolservice.example/
https://www.dravenspoolresurfacing.example/pool-renovation-ga/
Thank you for taking the time to consider designing a website for us. We are web developers based in Stockton, CA, USA. Most of our projects go through the same process. Understanding this process may help you win a project with us. We custom-code all of our websites in-house. We don’t have any requirements as to what tools you use for your design, but we prefer Figma files. For any design that we label as four-stars, we send it to the client for review. The client picks the final design they want us to use. Once we complete this process, we will continue to show additional clients all the four-star sites and purchase them later. Your designs will have multiple chances to sell. For better chances of success, we ask that you follow these guidelines.
IMAGES:
If you use any images or icons in the design, we ask that you have a link to the asset so we can purchase the image/icon. Most of the designs we submit do not have the customer’s images on them unless they have some great images. Be creative; show us the feeling you are trying to portray with your image choices. Use any royalty-free site you choose. We subscribe to Adobe and mainly use their images, but we can purchase images outside of Adobe. PLEASE NOTE: we will not submit designs to clients with watermarks on the images.
FONTS:
We ask that you identify the fonts used in the design. This can be done in a message if you want. We typically use Google Fonts and Adobe Fonts.
CONTENT:
We're always open to different content and ideas. We often submit designs with stock images so the client can see our vision. We typically take pictures after the website launch to use their images with our vision. Lorem Ipsum is fine for paragraphs, but we ask that you write the headers in correct English. We want to be able to show the vision and identify the sections of the website.
INSPIRATION:
We typically add a couple of links in the brief of websites we like to help you get started in your design.
REVISIONS:
We do not often ask for revisions of the designs unless we see something in the design that may not appeal to the client. If there are slight changes that we want to make, we do that in the development process.
FEEDBACK:
We rarely give feedback on designs during the design process. We are working on many website projects and do not have the time to provide feedback. We usually respond if your request is well thought out and asks specific questions, but a note asking “feedback, please” usually goes unanswered.
Number of Pages Required
1 page
Look and feel
Each slider illustrates characteristics of the customer's brand and the style your logo design should communicate.

```html
<!DOCTYPE html>
<html lang="en">
<head>
<meta charset="utf-8">
<title>Marlow Pool Service</title>
<link href="https://fonts.googleapis.com/css2?family=Fira+Sans:wght@500;600&family=Open+Sans:wght@400;600;700&display=swap" rel="stylesheet">
<style>
:root{
  --navy:#1c3f77;
  --blue:#1e8ff0;
  --ink:#222a35;
  --muted:#6b7380;
  --grey:#f1f1f1;
  --dark:#0f1c2b;
  --white:#fff;
  --line:#d9dde3;
}
*{box-sizing:border-box;margin:0;padding:0}
html,body{width:1200px;height:4967px;overflow:hidden}
body{position:relative;font-family:"Open Sans",sans-serif;color:var(--ink);background:var(--white)}
.abs{position:absolute}
h1,h2,h3,h4{font-family:"Fira Sans",sans-serif;font-weight:600}
.label{font-size:11px;font-weight:700;color:var(--blue);letter-spacing:.5px;text-transform:uppercase;display:flex;align-items:center;gap:14px}
.label .dash{display:inline-block;width:46px;height:2px;background:var(--blue)}
.section-title{color:var(--navy);font-size:46px;line-height:1.2}
.btn{display:flex;align-items:center;justify-content:center;font-weight:700;font-size:13px;border-radius:4px}
.btn-blue{background:var(--blue);color:var(--white)}
.lorem{font-size:12.5px;line-height:24px;color:var(--muted)}
.photo{overflow:hidden}

/* header */
.topbar{left:0;top:0;width:1200px;height:106px;background:#f4f4f4}
.brand{left:96px;top:30px;font-family:"Fira Sans",sans-serif;font-weight:500;font-size:22px;color:var(--blue);display:flex;align-items:center;gap:8px}
.brand .mark{width:14px;height:14px;border-radius:50%;background:var(--blue)}
.info{display:flex;gap:14px;align-items:center;font-size:11px;color:#444}
.info b{display:block;font-size:10px;font-weight:600;color:#555;text-transform:uppercase}
.quote{left:946px;top:22px;width:166px;height:46px;background:#2a2e33;color:#fff;font-size:11px;border-radius:4px}
.nav{left:87px;top:73px;width:1026px;height:68px;background:#fff;box-shadow:0 4px 16px rgba(0,0,0,.08);display:flex;align-items:center;padding-left:36px;z-index:2}
.nav a{font-size:13px;font-weight:700;color:#333;text-decoration:none;margin-right:58px}
.social{display:flex;gap:10px;position:absolute;right:30px;top:18px}
.social span{width:34px;height:34px;border-radius:3px}
/* hero */
.hero{left:0;top:106px;width:1200px;height:687px;background:linear-gradient(120deg,#7c6a4e 0%,#4a5a5a 35%,#2f6c7c 60%,#5a8a9a 100%)}
.hero .shade{position:absolute;inset:0;background:rgba(10,20,30,.35)}
.welcome{left:512px;top:330px;width:162px;height:36px;background:var(--navy);color:#fff;font-size:11px;font-weight:600;border-radius:3px}
.hero-title{position:absolute;left:0;top:380px;width:1200px;text-align:center;color:#fff;font-size:62px;line-height:72px;letter-spacing:1px}
.about-btn{left:508px;top:547px;width:170px;height:48px;border:2px solid #fff;color:#fff;font-size:11px;border-radius:3px}
.arrow-box{width:60px;height:60px;background:#fff;display:flex;align-items:center;justify-content:center}
/* about */
.about-photo{left:96px;top:922px;width:444px;height:433px;border-radius:50%;background:radial-gradient(circle at 45% 40%,#c8ccd2,#6d88a7 60%,#2f3e52);border-left:12px solid var(--navy)}
.trident-badge{left:432px;top:1248px;width:100px;height:100px;border-radius:50%;background:#fff;box-shadow:0 4px 14px rgba(0,0,0,.15);display:flex;align-items:center;justify-content:center}
.trident-badge span{width:22px;height:22px;border-radius:50%;background:var(--blue)}
/* services */
.services-bg{left:0;top:1457px;width:1200px;height:826px;background:var(--grey)}
.card{width:320px;height:313px;border-radius:8px;color:#fff;padding:0 34px}
.card .icon{position:absolute;left:40px;top:46px;width:66px;height:66px;background:#fff;border-radius:6px;display:flex;align-items:center;justify-content:center}
.card h3{position:absolute;left:34px;top:146px;font-size:22px}
.card p{position:absolute;left:34px;top:212px;font-size:12px}
.card a{position:absolute;left:34px;top:246px;font-size:14px;font-weight:700}
.card .bar{position:absolute;left:34px;top:281px;width:250px;height:3px;background:var(--blue)}
.card .veil{position:absolute;inset:0;background:linear-gradient(180deg,rgba(20,35,55,.25),rgba(20,35,55,.75));border-radius:8px}
.cta{left:95px;top:2179px;width:1015px;height:208px;border-radius:8px;background:linear-gradient(90deg,#18212c,#3a3a35 50%,#2a2620)}
/* why */
.why-item h4{color:var(--navy);font-size:20px;font-weight:500}
.why-item p{font-size:12.5px;line-height:20px;color:var(--muted);margin-top:6px}
.why-icon{width:76px;height:76px;border-radius:50%;background:#fff;box-shadow:0 4px 16px rgba(0,0,0,.1);display:flex;align-items:center;justify-content:center}
/* testimonials */
.testi-bg{left:0;top:3059px;width:1200px;height:533px;background:var(--grey)}
.testi-dark{left:0;top:3059px;width:336px;height:533px;background:linear-gradient(160deg,#3a3f44,#1f2226)}
.tcard{top:3262px;width:344px;height:204px;background:#fff;border-radius:8px;box-shadow:0 6px 20px rgba(0,0,0,.06);padding:24px}
.tcard p{font-size:12px;line-height:24px;color:var(--muted)}
.person{display:flex;align-items:center;gap:14px;margin-top:12px;font-size:11.5px;font-weight:700}
.avatar{width:44px;height:44px;border-radius:50%;background:#b9a996}
.qmark{position:absolute;right:28px;bottom:46px;font-family:"Fira Sans",sans-serif;font-size:44px;color:var(--navy);line-height:1}
/* contact */
.contact-box{left:93px;top:3847px;width:1013px;height:413px;background:#fff;box-shadow:0 6px 30px rgba(0,0,0,.08)}
.field{height:47px;border:1px solid var(--line);border-radius:4px;font-size:12px;color:#777;padding:0 18px;display:flex;align-items:center}
/* footer */
.footer{left:0;top:4406px;width:1200px;height:506px;background:var(--dark)}
.reach{left:85px;top:4406px;width:1029px;height:153px;background:#fff;display:flex}
.reach div{flex:1;display:flex;flex-direction:column;align-items:center;justify-content:center;gap:14px;font-weight:700;font-size:15px;border-right:1px solid #e6e6e6}
.reach div:last-child{border:none}
.foot-h{font-size:17px;color:#fff;font-weight:600}
.foot-link{font-size:12.5px;color:#9aa4b0;line-height:34px}
.bottom{left:0;top:4912px;width:1200px;height:55px;background:#dfe6ef;font-size:11px;font-weight:700;display:flex;align-items:center;padding-left:86px}
</style>
</head>
<body>

<!-- Header -->
<div class="abs topbar"></div>
<div class="abs brand"><span class="mark"></span>Marlow Pool Service</div>
<div class="abs info" style="left:430px;top:24px">
  <svg width="26" height="32" viewBox="0 0 24 30"><path d="M12 1C6 1 2 5.5 2 11c0 7 10 18 10 18s10-11 10-18C22 5.5 18 1 12 1z" fill="#333"/><circle cx="12" cy="11" r="4" fill="#f4f4f4"/></svg>
  <div><b>Location</b>214 Kelso Rd, LA</div>
</div>
<div class="abs" style="left:652px;top:22px;width:1px;height:44px;background:#ccc"></div>
<div class="abs info" style="left:676px;top:24px">
  <svg width="36" height="36" viewBox="0 0 36 36"><circle cx="18" cy="18" r="15" fill="none" stroke="#333" stroke-width="3"/><path d="M18 9v10l7 4" stroke="#333" stroke-width="3" fill="none"/></svg>
  <div><b>Office Hours</b>9.00 to 7.00 [Ssun: closed]</div>
</div>
<div class="abs btn quote">REQUEST A QUOTE</div>

<!-- Hero -->
<div class="abs hero photo" role="img" aria-label="Woman relaxing at the edge of a sunlit swimming pool"><div class="shade"></div></div>
<nav class="abs nav">
  <a>Home</a><a>About Us</a><a>Services</a><a>Gallery</a><a>Our Team</a><a>Contact Us</a>
  <div class="social"><span style="background:#2f5fb3"></span><span style="background:#e02b2b"></span><span style="background:#2aa3ef"></span></div>
</nav>
<div class="abs btn welcome">WELCOME</div>
<h1 class="hero-title">Crafting Memories,<br>One Pool at a Time</h1>
<div class="abs btn about-btn">ABOUT COMPANY</div>
<div class="abs arrow-box" style="left:44px;top:489px"><svg width="22" height="16"><path d="M21 8H2M8 2L2 8l6 6" stroke="#999" stroke-width="1.6" fill="none"/></svg></div>
<div class="abs arrow-box" style="left:1096px;top:489px"><svg width="22" height="16"><path d="M1 8h19M14 2l6 6-6 6" stroke="#999" stroke-width="1.6" fill="none"/></svg></div>

<!-- About -->
<div class="abs about-photo" role="img" aria-label="Pool technician working with tools beside a pool"></div>
<div class="abs trident-badge"><span></span></div>
<div class="abs label" style="left:612px;top:940px">About Us <span class="dash"></span></div>
<h2 class="abs section-title" style="left:609px;top:972px;width:520px;line-height:60px">Innovating Aquatic Elegance</h2>
<p class="abs lorem" style="left:612px;top:1106px;width:446px">Lorem ipsum dolor sit amet, consectetur adipiscing elit, sed do eiusmo empor incididunt ut abore et dolore magna aliqua. Ut enim ad minim iam, quis nostrud exercitation ullamco</p>
<p class="abs lorem" style="left:612px;top:1188px;width:446px">Lorem ipsum dolor sit amet, consectetur adipiscing elit, sed do eiusmo empor incididunt ut abore et dolore magna aliqua. Ut enim ad minim iam, quis nostrud exercitation ullamco</p>
<div class="abs btn btn-blue" style="left:612px;top:1295px;width:168px;height:45px">Apply Now</div>

<!-- Services -->
<div class="abs services-bg"></div>
<div class="abs label" style="left:90px;top:1543px">Services <span class="dash"></span></div>
<h2 class="abs section-title" style="left:88px;top:1575px">Services We Offer</h2>
<div class="abs arrow-box" style="left:1000px;top:1559px;width:46px;height:62px"><svg width="10" height="16"><path d="M8 1L2 8l6 7" stroke="#222" stroke-width="2" fill="none"/></svg></div>
<div class="abs arrow-box" style="left:1052px;top:1559px;width:46px;height:62px"><svg width="10" height="16"><path d="M2 1l6 7-6 7" stroke="#222" stroke-width="2" fill="none"/></svg></div>

<div class="abs card photo" style="left:93px;top:1683px;background:linear-gradient(135deg,#5a7f9a,#2c4d6c)" role="img" aria-label="Tiled pool wall being repaired">
  <div class="veil"></div>
  <div class="icon"><svg width="34" height="34" viewBox="0 0 24 24"><path d="M12 3l2.6 5.4 5.9.8-4.3 4.1 1 5.8L12 16.3 6.8 19l1-5.8L3.5 9.2l5.9-.8z" fill="none" stroke="#1c3f77" stroke-width="1.5"/></svg></div>
  <h3>Pool Repair</h3><p>Lorem ipsum dolor sit amet, consectetur</p><a>Read More</a><div class="bar"></div>
</div>
<div class="abs card photo" style="left:440px;top:1683px;background:linear-gradient(135deg,#9a8e78,#4e5a5e)" role="img" aria-label="Construction workers in safety helmets">
  <div class="veil"></div>
  <div class="icon"><svg width="34" height="34" viewBox="0 0 24 24"><path d="M4 20h16M8 17l9-9-3-3-9 9v3z" fill="none" stroke="#1c3f77" stroke-width="1.5"/></svg></div>
  <h3>Pool Construction</h3><p>Lorem ipsum dolor sit amet, consectetur</p><a>Read More</a><div class="bar"></div>
</div>
<div class="abs card photo" style="left:787px;top:1683px;background:linear-gradient(135deg,#a88a6a,#3f8a9c 60%,#2a5a6a)" role="img" aria-label="Clean backyard pool on a sunny day">
  <div class="veil"></div>
  <div class="icon"><svg width="34" height="34" viewBox="0 0 24 24"><circle cx="9" cy="8" r="3" fill="none" stroke="#1c3f77" stroke-width="1.5"/><circle cx="16" cy="9" r="2.5" fill="none" stroke="#1c3f77" stroke-width="1.5"/><path d="M3 19c0-3 3-5 6-5s6 2 6 5M14 14c3 0 6 1.5 6 4" fill="none" stroke="#1c3f77" stroke-width="1.5"/></svg></div>
  <h3>Pool Cleaning</h3><p>Lorem ipsum dolor sit amet, consectetur</p><a>Read More</a><div class="bar"></div>
</div>
<div class="abs btn btn-blue" style="left:513px;top:2069px;width:168px;height:46px">Contact Us</div>

<div class="abs cta photo" role="img" aria-label="Evening view of a lit indoor pool"></div>
<h3 class="abs" style="left:150px;top:2258px;color:#fff;font-size:23px;line-height:28px">Inspired Designs,<br>Impeccable Craftsmanship</h3>
<div class="abs btn" style="left:683px;top:2264px;width:164px;height:52px;border:2px solid #fff;color:#fff;font-weight:600">Get A Quote</div>
<div class="abs btn" style="left:855px;top:2264px;width:205px;height:52px;background:#fff;color:#222;font-weight:600;gap:10px">
  <svg width="16" height="16" viewBox="0 0 24 24"><path d="M5 3l4 1 1 5-2 1a11 11 0 006 6l1-2 5 1 1 4c-10 1-17-6-16-16z" fill="#222"/></svg>+ 012 555 - 01840</div>

<!-- Why choose us -->
<div class="abs label" style="left:506px;top:2452px">
  <span class="dash"></span>Why Us<span class="dash"></span></div>
<h2 class="abs section-title" style="left:0;top:2475px;width:1200px;text-align:center">Why Choose Us</h2>
<svg class="abs" style="left:340px;top:2600px" width="520" height="330" viewBox="0 0 520 330">
  <path d="M52 70 Q10 156 52 270" fill="none" stroke="#bbb" stroke-width="1.5"/>
  <path d="M468 70 Q510 156 468 270" fill="none" stroke="#bbb" stroke-width="1.5"/>
</svg>
<div class="abs photo" style="left:430px;top:2592px;width:328px;height:328px;border-radius:50%;background:radial-gradient(circle at 50% 40%,#b8b4ae,#3f5a86 70%)" role="img" aria-label="Smiling team leader in a grey suit"></div>

<div class="abs why-item" style="left:110px;top:2616px;width:200px;text-align:right"><h4>Quality Assurance</h4><p>Lorem ipsum dolor sit amet,<br>consectetur adipiscing</p></div>
<div class="abs why-item" style="left:80px;top:2741px;width:200px;text-align:right"><h4>Proven Record</h4><p>Lorem ipsum dolor sit amet,<br>consectetur adipiscing</p></div>
<div class="abs why-item" style="left:60px;top:2866px;width:240px;text-align:right"><h4>Personalized Approach</h4><p>Lorem ipsum dolor sit amet,<br>consectetur adipiscing</p></div>
<div class="abs why-item" style="left:874px;top:2606px;width:260px"><h4>Comprehensive Services</h4><p>Lorem ipsum dolor sit amet,<br>consectetur adipiscing</p></div>
<div class="abs why-item" style="left:897px;top:2741px;width:240px"><h4>Professionalism</h4><p>Lorem ipsum dolor sit amet,<br>consectetur adipiscing</p></div>
<div class="abs why-item" style="left:874px;top:2866px;width:260px"><h4>Experience and Expertise</h4><p>Lorem ipsum dolor sit amet,<br>consectetur adipiscing</p></div>

<div class="abs why-icon" style="left:354px;top:2611px"><svg width="32" height="32" viewBox="0 0 24 24"><path d="M5 17a8 8 0 1114 0M12 12l2-4" fill="none" stroke="#1e8ff0" stroke-width="1.5"/></svg></div>
<div class="abs why-icon" style="left:321px;top:2736px"><svg width="32" height="32" viewBox="0 0 24 24"><path d="M12 3l2.6 5.4 5.9.8-4.3 4.1 1 5.8L12 16.3 6.8 19l1-5.8L3.5 9.2l5.9-.8z" fill="none" stroke="#1e8ff0" stroke-width="1.5"/></svg></div>
<div class="abs why-icon" style="left:354px;top:2861px"><svg width="32" height="32" viewBox="0 0 24 24"><path d="M4 20h16M8 17l9-9-3-3-9 9v3z" fill="none" stroke="#1e8ff0" stroke-width="1.5"/></svg></div>
<div class="abs why-icon" style="left:761px;top:2611px"><svg width="32" height="32" viewBox="0 0 24 24"><circle cx="9" cy="8" r="3" fill="none" stroke="#1e8ff0" stroke-width="1.5"/><circle cx="16" cy="9" r="2.5" fill="none" stroke="#1e8ff0" stroke-width="1.5"/><path d="M3 19c0-3 3-5 6-5s6 2 6 5M14 14c3 0 6 1.5 6 4" fill="none" stroke="#1e8ff0" stroke-width="1.5"/></svg></div>
<div class="abs why-icon" style="left:794px;top:2736px"><svg width="32" height="32" viewBox="0 0 24 24"><circle cx="12" cy="13" r="8" fill="none" stroke="#1e8ff0" stroke-width="1.5"/><path d="M12 13l4-3" stroke="#1e8ff0" stroke-width="1.5"/></svg></div>
<div class="abs why-icon" style="left:761px;top:2861px"><svg width="32" height="32" viewBox="0 0 24 24"><path d="M19 12a7 7 0 01-12 5M5 12a7 7 0 0112-5M17 3v4h-4M7 21v-4h4" fill="none" stroke="#1e8ff0" stroke-width="1.5"/></svg></div>

<!-- Testimonials -->
<div class="abs testi-bg"></div>
<div class="abs testi-dark photo" role="img" aria-label="Dim poolside lounge backdrop"></div>
<div class="abs label" style="left:576px;top:3120px;gap:0"><span class="dash"></span>Testimonials<span class="dash"></span></div>
<h2 class="abs section-title" style="left:336px;top:3145px;width:660px;text-align:center">Reviews from Clients</h2>

<div class="abs tcard" style="left:135px"><p>Lorem ipsum dolorLorem ipsum dolor sit amet, consectetur adipiscing elit, sed do eiusmod tempor incididunt ut labore et dolore magna aliqua. Ut en im ad minim veniam, quis nostrud exercitation ull</p><div class="person"><span class="avatar"></span>Owen Fairley</div><span class="qmark">”</span></div>
<div class="abs tcard" style="left:502px;border-bottom:3px solid var(--blue)"><p>Lorem ipsum dolorLorem ipsum dolor sit amet, consectetur adipiscing elit, sed do eiusmod tempor incididunt ut labore et dolore magna aliqua. Ut en im ad minim veniam, quis nostrud exercitation ull</p><div class="person"><span class="avatar" style="background:#8f8a86"></span>Owen Fairley</div><span class="qmark">”</span></div>
<div class="abs tcard" style="left:870px;width:344px"><p>Lorem ipsum dolorLorem ipsum dolor sit amet, consectetur adipiscing elit, sed do eiusmod tempor incididunt ut labore et dolore magna aliqua. Ut en im ad minim veniam, quis nostrud exercitation ull</p><div class="person"><span class="avatar" style="background:#c9a58a"></span>Owen Fairley</div><span class="qmark" style="right:42px">”</span></div>
<svg class="abs" style="left:626px;top:3505px" width="110" height="20"><circle cx="10" cy="10" r="7" fill="none" stroke="#1e8ff0" stroke-width="1.5"/><circle cx="10" cy="10" r="3" fill="#1e8ff0"/><circle cx="40" cy="10" r="3" fill="#aaa"/><circle cx="70" cy="10" r="3" fill="#aaa"/><circle cx="100" cy="10" r="3" fill="#aaa"/></svg>

<!-- Contact -->
<div class="abs label" style="left:530px;top:3716px"><span class="dash"></span>Contact Us<span class="dash"></span></div>
<h2 class="abs section-title" style="left:0;top:3739px;width:1200px;text-align:center">Get in touch with us</h2>
<div class="abs contact-box"></div>
<div class="abs photo" style="left:93px;top:3847px;width:417px;height:413px;background:linear-gradient(160deg,#3fc0d8,#1a9ab8 55%,#b89a78)" role="img" aria-label="Woman in a sun hat sitting at the pool edge"></div>
<div class="abs btn" style="left:286px;top:4180px;width:197px;height:56px;background:#fff;color:#222;font-size:17px;gap:12px;border-radius:3px">
  <svg width="18" height="18" viewBox="0 0 24 24"><path d="M5 3l4 1 1 5-2 1a11 11 0 006 6l1-2 5 1 1 4c-10 1-17-6-16-16z" fill="#222"/></svg>1800-555-014</div>
<h3 class="abs" style="left:552px;top:3892px;font-size:24px;color:#333">Get Free Consultation</h3>
<p class="abs" style="left:552px;top:3930px;width:500px;font-size:13px;line-height:25px;color:var(--muted)">Get a free consultation from our experts, Our customer support team help you 24/7. Don't hesitate.</p>
<div class="abs field" style="left:552px;top:4014px;width:502px">Your Name</div>
<div class="abs field" style="left:552px;top:4084px;width:238px">Your Email</div>
<div class="abs field" style="left:816px;top:4084px;width:238px">Message</div>
<div class="abs btn btn-blue" style="left:552px;top:4151px;width:502px;height:49px;font-size:11px;gap:8px">GET IN TOUCH <svg width="18" height="10"><path d="M0 5h16M12 1l4 4-4 4" stroke="#fff" stroke-width="1.5" fill="none"/></svg></div>

<!-- Footer -->
<svg class="abs" style="left:0;top:4370px" width="1200" height="40"><path d="M118 4L1114 30V40H108z" fill="#e3e8ef"/></svg>
<div class="abs footer"></div>
<div class="abs reach">
  <div><svg width="44" height="40" viewBox="0 0 44 40"><path d="M22 2c-7 0-12 5-12 11 0 8 12 20 12 20s12-12 12-20c0-6-5-11-12-11z" fill="none" stroke="#1e8ff0" stroke-width="2"/><circle cx="22" cy="13" r="4" fill="none" stroke="#1e8ff0" stroke-width="2"/><path d="M4 38l6-10h24l6 10z" fill="none" stroke="#1e8ff0" stroke-width="2"/></svg>Come to Our Location</div>
  <div><svg width="44" height="40" viewBox="0 0 44 40"><rect x="4" y="8" width="36" height="28" fill="none" stroke="#1e8ff0" stroke-width="2"/><path d="M4 8l18 16L40 8" fill="none" stroke="#1e8ff0" stroke-width="2"/></svg>Send Us an Email</div>
  <div><svg width="44" height="40" viewBox="0 0 24 24"><path d="M5 3l4 1 1 5-2 1a11 11 0 006 6l1-2 5 1 1 4c-10 1-17-6-16-16z" fill="none" stroke="#1e8ff0" stroke-width="1.3"/></svg>Give Us a Call</div>
</div>
<div class="abs" style="left:108px;top:4680px;font-family:'Fira Sans',sans-serif;font-weight:500;font-size:24px;color:#fff;display:flex;align-items:center;gap:10px"><span style="width:14px;height:14px;border-radius:50%;background:#fff"></span>Marlow Pool Service</div>
<p class="abs" style="left:85px;top:4736px;width:310px;font-size:12.5px;line-height:22px;color:#9aa4b0">Lorem ipsum dolor sit amet, consectetur adipiscing elit, sed do eiusmod tempor incididunt ut labore et dolore magna aliqua. Ut enim ad minim veniam, quis nostrud exercitation ullamco laboris</p>
<h4 class="abs foot-h" style="left:438px;top:4616px">Visit Our Place</h4>
<p class="abs" style="left:438px;top:4680px;font-size:12.5px;line-height:22px;color:#9aa4b0">57 Harbor Lane<br>Suite 4, 10021, USA</p>
<p class="abs" style="left:438px;top:4740px;font-size:11px;font-weight:700;color:#fff;text-decoration:underline">FIND US ON MAP</p>
<div class="abs" style="left:438px;top:4774px;width:306px;height:42px;border:1px solid #5a6575;display:flex">
  <span style="flex:1;font-size:11px;color:#9aa4b0;padding:13px 12px">Enter Your Email...</span>
  <span style="width:106px;border-left:1px solid #5a6575;color:#1e8ff0;font-size:12px;font-weight:700;display:flex;align-items:center;justify-content:center">SUBSCRIBE</span>
</div>
<h4 class="abs foot-h" style="left:790px;top:4616px">Useful Links</h4>
<div class="abs foot-link" style="left:788px;top:4672px">About Us<br>Practice areas<br>Why Choose Us<br>How it works<br>News &amp; Updates</div>
<div class="abs foot-link" style="left:958px;top:4672px">Testimonials<br>FAQs<br>Cookies<br>Contact Us<br>Privacy Policy</div>
<div class="abs bottom">Marlow Pool Service</div>
<svg class="abs" style="left:1036px;top:4932px" width="80" height="12"><rect x="0" y="2" width="8" height="8" fill="#222"/><rect x="22" y="2" width="8" height="8" fill="#222"/><rect x="44" y="2" width="8" height="8" fill="#222"/><rect x="66" y="2" width="8" height="8" fill="#222"/></svg>
<div class="abs btn btn-blue" style="left:1139px;top:4902px;width:48px;height:48px"><svg width="18" height="12"><path d="M2 10l7-7 7 7" stroke="#fff" stroke-width="3" fill="none"/></svg></div>

</body>
</html>
```